Flyer - Pellwyn Dental Orrick

** Please do not use my words - word-for-word on the flyer design **
We have recently bought an established dental business. However we are not getting new customers through the door. We plan to implement aggressive local marketing strategies including flyer distribution. We are looking for an eye-catching must read flyer design. Some details & content ideas are as below.
1. A5 size - Double Sided
2. Our business name is Pellwyn Dental Orrick. Logo is attached. Website is www.pellwyndentalorrick.com.au where lot of useful information can be found.
3. Practice has a long & proud history serving "Lower North Shore" since 1958. We provide quality dental care at affordable prices.
4. List of services can be found on website
5. Perhaps a snippet of Plotmark Atlas Location would be useful. Also the fact that 3-hour free parking is available in Marrowby Arcade less than 100m away from practice. Plenty of 2-hours street parking is available too.
6. Opening hours can be found on website. Fact that we are open on Saturdays and till late on Tuesdays is worth calling out.
7. We would like to run a campaign of offers with this flyer. Give it a name! Details below.
a) NO GAP Checkup and Clean with any major Private Health Fund. Includes oral exam, 2 X-Rays, Scale & Polish and Fluoride Treatment
b) Genuine Teeth Whitening for $199 (usually $399 save $200)
c) 10% off on all major dental. Includes fillings, crowns, bridges and root canal treatment
8. We are HEXA Preferred Provider means HEXA members get maximum benefit. HEXA Loyal Tier logo attached.
9. We participate in Office for Former Forces Care Fee Schedule. Logo attached.
10. Call out WE ACCEPT ALL HEALTH FUNDS
Dental
- Helvetica Neue, Myriad Pro

```html
<!DOCTYPE html>
<html lang="en">
<head>
<meta charset="utf-8">
<title>Pellwyn Dental Orrick – Flyer Back</title>
<link rel="stylesheet" href="https://fonts.googleapis.com/css2?family=PT+Sans:wght@400;700&display=swap">
<style>
  :root {
    --lime: #a9cf46;
    --teal: #5cc39f;
    --ink: #111111;
    --rule: #222222;
    --paper: #ffffff;
    --tint: #e6f5f0;
  }
  * { margin: 0; padding: 0; box-sizing: border-box; }
  html, body { width: 1200px; height: 1000px; overflow: hidden; background: var(--paper); }
  body { font-family: "PT Sans", "Myriad Pro", Arial, sans-serif; color: var(--ink); position: relative; }
  .flyer {
    position: absolute; left: 248px; top: 0; width: 708px; height: 1000px;
    border-left: 1px solid var(--rule); border-right: 1px solid var(--rule);
    background: var(--paper);
  }
  .flyer__pattern {
    position: absolute; inset: 0;
    background: radial-gradient(ellipse at 50% 50%, var(--tint) 0%, rgba(230,245,240,0.35) 55%, rgba(255,255,255,0) 100%);
    opacity: 0.55;
  }
  .block { position: absolute; }
  .centered { left: 0; width: 708px; text-align: center; }
  .heading { font-weight: 700; font-size: 18px; line-height: 24px; color: var(--lime); text-transform: uppercase; }
  .heading--teal { color: var(--teal); }
  .fund-list { font-size: 18px; line-height: 24.5px; text-transform: uppercase; }
  .body-text { font-size: 18.5px; line-height: 24.5px; }
  .offer { left: 42px; top: 193px; width: 640px; }
  .child-benefit { left: 47px; top: 313px; width: 620px; }
  .address { font-weight: 700; font-size: 26px; line-height: 32px; color: var(--teal); }
  .location { left: 47px; top: 516px; width: 330px; }
  .map {
    position: absolute; left: 412px; top: 503px; width: 256px; height: 168px;
    background: linear-gradient(135deg, #ecebe6 0%, #e3e1da 60%, #dfe6d6 100%);
  }
  .map__pin { position: absolute; left: 118px; top: 70px; }
  .parking { left: 47px; top: 694px; width: 620px; }
  .hours-title { font-weight: 700; font-size: 18px; line-height: 24px; color: var(--lime); }
  .hours { font-size: 18px; line-height: 24.3px; }
  .call { font-weight: 700; font-size: 17px; color: var(--teal); line-height: 30px; }
  .call__number { font-size: 24px; }
  .call-note { font-size: 17.5px; line-height: 22px; }
</style>
</head>
<body>
  <main class="flyer">
    <div class="flyer__pattern" role="img" aria-label="Faint mint tooth outline pattern across the page"></div>

    <h2 class="block centered heading" style="top:49px;">We accept all health fund cards!</h2>
    <ul class="block centered fund-list" style="top:72px; list-style:none;">
      <li>HEXA &amp; NORVAL</li>
      <li>Former Forces Care</li>
      <li>Seniors Card</li>
      <li>Claimpoint</li>
    </ul>

    <p class="block body-text offer">NO GAP Checkup and Clean with any major Private Health Fund.<br>Includes oral exam, 2 X-Rays, Scale &amp; Polish and Fluoride Treatment</p>

    <h2 class="block centered heading" style="top:288px;">The Child Dental Benefit Schedule</h2>
    <p class="block body-text child-benefit">Paid by Carewell, provides access to benefits for basic dental services for eligible children. &nbsp;You can confirm your child’s eligibility by calling Carewell on 135 240.</p>

    <h2 class="block centered heading heading--teal" style="top:416px;">Contact us</h2>
    <p class="block centered address" style="top:442px;">86 Harlow Avenue Orrick NSW 2199</p>

    <p class="block body-text location">We are located 100m from Marrowby Arcade, and directly opposite Civic Desk and Glint Car Wash Café on the intersection of Harlow Avenue and Tamsin Street.</p>

    <div class="map" role="img" aria-label="Street map showing the practice location near Marrowby Arcade">
      <svg class="map__pin" width="12" height="18" viewBox="0 0 12 18" aria-hidden="true">
        <path d="M6 0C2.7 0 0 2.6 0 5.9 0 10.3 6 18 6 18s6-7.7 6-12.1C12 2.6 9.3 0 6 0z" fill="#d93a2b"/>
        <circle cx="6" cy="6" r="2.2" fill="#8e1c12"/>
      </svg>
    </div>

    <p class="block body-text parking">Marrowby Arcade with over 2500 car spaces offers convenient 3-hours free parking and there is also ample 2-hours street parking available.</p>

    <h3 class="block centered hours-title" style="top:767px;">Office Hours</h3>
    <ul class="block centered hours" style="top:792px; list-style:none;">
      <li>Monday 8:30am – 5:30pm</li>
      <li>Tuesday 12:00pm – 8:00pm</li>
      <li>Wednesday – Friday 8:30am – 5:30pm</li>
      <li>Saturday 9:00am – 4:00pm</li>
    </ul>

    <p class="block centered call" style="top:928px;">Call us on <span class="call__number">(02) 5550 1836</span></p>
    <p class="block centered call-note" style="top:957px;">to book an appointment now!</p>
  </main>
</body>
</html>
```